Business Card Design Project - Sports Brand

Brisk is a e-commerce fitness wear brand for ladies who are into gym, pole and swim.

Card should not be overly cluttered and should include the following:

1. logo
2. Name of the company (Use "Brisk Loom Pte Ltd" for now)
3. Address of company (Use a mock address)
4. Representative's name and contact info etc. (use a mock name and contact info)
5. website address

Target Market(s)

Women who are into pole , gym, and swim.

Women who shop online

Industry/Entity Type

E-Commerce

Colors

Designer to choose colors to be used in the design.

Requirements
Nice to have
• feminine sublimation of colours

Need not be printed on traditional paper. We would like the design to be revolutionary and interesting to the eye :)
Should not have
• the design should not be traditional looking. Do not include illustrations of Bikinis, yoga poses etc. in the card.

```html
<!DOCTYPE html>
<html lang="en">
<head>
<meta charset="utf-8">
<title>Brisk Loom Pte Ltd – Business Card</title>
<link rel="stylesheet" href="https://fonts.googleapis.com/css2?family=Lato:wght@300;400;700;900&display=swap">
<style>
  :root {
    --backdrop: #2b2b2d;
    --card-white: #fbfbfb;
    --pink: #e08bb6;
    --pink-deep: #d27aa7;
    --stripe: #ffffff;
    --brand-red: #b3263a;
    --brand-dot: #ec6a7c;
    --ink: #111111;
    --ink-soft: #f6e6ef;
  }
  * { margin: 0; padding: 0; box-sizing: border-box; }
  html, body {
    width: 1200px; height: 900px; overflow: hidden;
    background: var(--backdrop);
    font-family: "Lato", Arial, sans-serif;
  }
  .card {
    position: absolute;
    width: 560px; height: 320px;
    border-radius: 22px;
    overflow: hidden;
    background: var(--card-white);
    box-shadow: 0 18px 40px rgba(0,0,0,.55);
  }

  /* ---------- front ---------- */
  .card--front { left: 90px; top: 100px; }
  .front__band {
    position: absolute; left: 0; right: 0; bottom: 0; height: 112px;
    background: var(--pink);
  }
  .front__stripes {
    position: absolute; left: 0; right: 0; bottom: 112px; height: 22px;
    background:
      linear-gradient(var(--pink), var(--pink)) 0 0 / 100% 4px no-repeat,
      linear-gradient(var(--pink), var(--pink)) 0 10px / 100% 4px no-repeat,
      linear-gradient(var(--pink), var(--pink)) 0 20px / 100% 2px no-repeat;
  }
  .front__company {
    position: absolute; left: 0; right: 0; bottom: 34px;
    text-align: center;
    font-weight: 300; font-size: 40px; letter-spacing: .5px;
    color: rgba(255,255,255,.72);
  }
  .brand {
    position: absolute;
    display: flex; align-items: center; gap: 14px;
  }
  .brand__dot {
    border-radius: 50%;
    background: var(--brand-dot);
  }
  .brand__name {
    font-weight: 700; color: var(--brand-red); letter-spacing: .5px;
  }
  .card--front .brand { left: 150px; top: 62px; }
  .card--front .brand__dot { width: 86px; height: 86px; }
  .card--front .brand__name { font-size: 58px; }

  /* ---------- back ---------- */
  .card--back { left: 550px; top: 480px; }
  .back__panel {
    position: absolute; top: 0; bottom: 0; right: 0; width: 300px;
    background: var(--pink);
  }
  .back__stripes {
    position: absolute; top: 0; bottom: 0; left: 244px; width: 16px;
    background:
      linear-gradient(var(--pink-deep), var(--pink-deep)) 0 0 / 4px 100% no-repeat,
      linear-gradient(var(--pink-deep), var(--pink-deep)) 10px 0 / 4px 100% no-repeat;
  }
  .card--back .brand { left: 34px; top: 82px; gap: 10px; }
  .card--back .brand__dot { width: 70px; height: 70px; }
  .card--back .brand__name { font-size: 46px; }
  .back__web {
    position: absolute; left: 32px; bottom: 32px;
    font-weight: 900; font-size: 21px; color: var(--ink);
  }
  .back__web .accent { color: var(--pink-deep); }
  .person { position: absolute; left: 300px; top: 36px; }
  .person__name {
    font-weight: 900; font-size: 20px; letter-spacing: .5px; color: #fff;
  }
  .person__role {
    font-weight: 900; font-size: 12px; letter-spacing: .6px; color: var(--ink);
    margin-left: 44px; margin-top: 2px;
  }
  .contact {
    position: absolute; left: 300px; top: 158px;
    list-style: none;
    color: var(--ink-soft); font-size: 15px; line-height: 1.35;
  }
  .contact li { display: flex; align-items: flex-start; gap: 8px; margin-bottom: 4px; }
  .contact svg { flex: none; width: 20px; height: 16px; margin-top: 2px; }
</style>
</head>
<body>

<section class="card card--front" aria-label="Card front">
  <div class="brand">
    <span class="brand__dot"></span>
    <span class="brand__name">Brisk</span>
  </div>
  <div class="front__stripes"></div>
  <div class="front__band"></div>
  <p class="front__company">Brisk Loom Pte Ltd</p>
</section>

<section class="card card--back" aria-label="Card back">
  <div class="brand">
    <span class="brand__dot"></span>
    <span class="brand__name">Brisk</span>
  </div>
  <p class="back__web">www.<span class="accent">briskloom</span>.com</p>

  <div class="back__stripes"></div>
  <div class="back__panel"></div>

  <div class="person">
    <p class="person__name">LENA HARTWELL</p>
    <p class="person__role">DESIGNATION</p>
  </div>

  <ul class="contact">
    <li>
      <svg viewBox="0 0 20 16" fill="none" stroke="currentColor" stroke-width="1.4">
        <rect x="1" y="1" width="18" height="14" rx="2"/>
        <path d="M5 6c0-2 10-2 10 0M6 11h8M7 8h6"/>
      </svg>
      <span>0400555019</span>
    </li>
    <li>
      <svg viewBox="0 0 20 16" fill="none" stroke="currentColor" stroke-width="1.4">
        <rect x="1" y="1" width="18" height="14" rx="1"/>
        <path d="M1 2l9 7 9-7M1 15l7-6M19 15l-7-6"/>
      </svg>
      <span>info@briskloom.com</span>
    </li>
    <li>
      <svg viewBox="0 0 20 16" fill="none" stroke="currentColor" stroke-width="1.4">
        <rect x="1" y="1" width="18" height="14" rx="1"/>
        <path d="M4 8l6-5 6 5M6 7v6h8V7"/>
      </svg>
      <span>Ardens Court, Millbank Road,<br>Fernleigh, BT40 2KQ</span>
    </li>
  </ul>
</section>

</body>
</html>
```